Business card for a new innovative and professional lawn care business

We need a business card design for a new lawn care business in Halifax NS Canada. We offer lawn services in Halifax & Bedford. Our services offered include lawn care, garden services, and property maintenance. We take pride in our work and are experienced at what we do. I would like to see a design that is double sided. On the backside I would like the something simple (maybe my logo preferably on blackround (linked below) with website link, Facebook page or something). The front I want to include contact info:
Morgan Pell
phone 902-555-0148
email - brookvaleyards.ca
facebook - Facebook.com/brookvaleyards
Instagram maybe ? - instagram.com/brookvaleyard
Serving Halifax and Bedford for 5 years?
I don't want it to have too much information as I will be passing them out in aim to visit website, or call !
We do want it to include lawn care, garden services and property maintenance.
Basic, catchy, and modern looking !
Logo attached below !

Target Market(s)

Passing business cards to everyone I meet or interact with.

Industry/Entity Type

Lawn Care

Contact Information for Business Card

Double sided with some basic information, with catchy colours and easy to look at.

Font styles to use
Sans Serif

Requirements
Must have
• Must be double sided and have :
• Name, Phone, Email, FB, Website, and 3 main services offered - lawn care, property maintenance, garden services
Nice to have
• Would be nice to have instagram link if it goes well on there
Should not have
• Don't want too much writing or images that are distracting

```html
<!DOCTYPE html>
<html lang="en">
<head>
<meta charset="utf-8">
<title>Brookvale Yards – Business Card</title>
<link href="https://fonts.googleapis.com/css2?family=Montserrat:wght@800&family=Open+Sans:wght@400;600&display=swap" rel="stylesheet">
<style>
  :root {
    --lime: #8cc63f;
    --forest: #1f7a3c;
    --ink: #050505;
    --paper: #ffffff;
    --stage: #e9ebe8;
  }
  * { margin: 0; padding: 0; box-sizing: border-box; }
  html, body {
    width: 1200px; height: 900px; overflow: hidden;
    background: var(--stage);
    font-family: "Open Sans", Arial, sans-serif;
  }
  .card {
    position: absolute; left: 250px;
    width: 700px; height: 400px;
    border-radius: 22px; overflow: hidden;
    box-shadow: 0 10px 28px rgba(0,0,0,.18);
  }
  .card-back { top: 30px; background: var(--ink); }
  .card-front { top: 470px; background: var(--paper); }

  .brand-name {
    font-family: "Montserrat", Arial, sans-serif;
    font-weight: 800; color: var(--lime);
    text-transform: uppercase; line-height: 1;
    letter-spacing: 1px; white-space: nowrap;
  }

  .brand-block {
    position: absolute; left: 0; right: 0; top: 140px;
    display: flex; flex-direction: column; align-items: center;
  }
  .brand-block .inner { display: flex; flex-direction: column; align-items: flex-end; gap: 16px; }
  .card-back .brand-name { font-size: 44px; }

  .social {
    color: var(--paper);
    font-size: 16px; display: flex; align-items: center; gap: 9px;
  }
  .social .mark { width: 12px; height: 12px; background: var(--lime); border-radius: 2px; }
  .social-facebook { position: absolute; left: 40px; bottom: 34px; }

  .card-front .brand-name { position: absolute; right: 44px; top: 32px; font-size: 34px; }

  .card-shape { position: absolute; inset: 0; }
  .mower-art {
    position: absolute; left: 38px; top: 190px;
    width: 118px; height: 150px;
    background: var(--forest); border-radius: 8px;
  }
  .owner-name {
    position: absolute; left: 178px; top: 272px;
    font-family: "Montserrat", Arial, sans-serif; font-weight: 800;
    font-size: 26px; color: var(--lime); text-transform: uppercase;
  }
  .contact-list {
    position: absolute; left: 178px; top: 312px;
    list-style: none; color: var(--paper); font-size: 15px; line-height: 23px;
  }
  .contact-list li { display: flex; align-items: center; gap: 9px; }
  .contact-list svg { width: 13px; height: 13px; flex: none; }

  .services {
    position: absolute; right: 40px; top: 205px;
    text-align: right; color: var(--paper); list-style: none;
    font-size: 15px; line-height: 22px;
  }
  .services-title {
    font-family: "Montserrat", Arial, sans-serif; font-weight: 800;
    color: var(--lime); font-size: 19px; text-transform: uppercase;
    margin-bottom: 2px; margin-right: 15px;
  }
  .service-item::after {
    content: ""; display: inline-block; width: 7px; height: 7px;
    border-radius: 50%; background: var(--lime); margin-left: 8px;
    vertical-align: middle;
  }
</style>
</head>
<body>

  <section class="card card-back" aria-label="Card back">
    <div class="brand-block">
      <div class="inner">
        <div class="brand-name">Brookvale Yards</div>
        <div class="social social-instagram"><span class="mark"></span>instagram.com/brookvaleyard</div>
      </div>
    </div>
    <div class="social social-facebook"><span class="mark"></span>Facebook.com/brookvaleyards</div>
  </section>

  <section class="card card-front" aria-label="Card front">
    <svg class="card-shape" viewBox="0 0 700 400" preserveAspectRatio="none" aria-hidden="true">
      <path fill="var(--lime)" d="M0 288 C220 138 470 52 645 80 C692 90 702 130 700 150 L700 400 L0 400 Z"/>
      <path fill="var(--ink)" d="M0 300 C220 160 470 82 640 102 C688 110 700 140 700 165 L700 400 L0 400 Z"/>
    </svg>
    <div class="brand-name">Brookvale Yards</div>
    <div class="mower-art" role="img" aria-label="Green lawn mower illustration"></div>

    <ul class="services">
      <li class="services-title">Services</li>
      <li class="service-item">Lawn care</li>
      <li class="service-item">Garden services</li>
      <li class="service-item">Property maintenance</li>
    </ul>

    <div class="owner-name">Morgan Pell</div>
    <ul class="contact-list">
      <li>
        <svg viewBox="0 0 24 24" fill="var(--lime)"><path d="M6.6 10.8a15.1 15.1 0 0 0 6.6 6.6l2.2-2.2a1 1 0 0 1 1-.25 11.4 11.4 0 0 0 3.6.57 1 1 0 0 1 1 1V20a1 1 0 0 1-1 1A17 17 0 0 1 3 4a1 1 0 0 1 1-1h3.5a1 1 0 0 1 1 1c0 1.25.2 2.45.57 3.57a1 1 0 0 1-.25 1z"/></svg>
        902-555-0148
      </li>
      <li>
        <svg viewBox="0 0 24 24" fill="none" stroke="var(--lime)" stroke-width="2.4"><rect x="2" y="5" width="20" height="14" rx="1"/><path d="M2 6l10 7 10-7"/></svg>
        info@brookvaleyards.ca
      </li>
      <li>
        <svg viewBox="0 0 24 24" fill="none" stroke="var(--lime)" stroke-width="2.2"><circle cx="12" cy="12" r="10"/><path d="M2 12h20M12 2c3 3 3 17 0 20M12 2c-3 3-3 17 0 20"/></svg>
        www.brookvaleyards.ca
      </li>
    </ul>
  </section>

</body>
</html>
```